Wine label for family vineyard start-up

Brand new family vineyard needs a new label:

The information we need on the label is the following:
- Merlot & Cabernet (variety)
- Ponte Capriasca (location)
- 2016 (vintage)

The style of the label should be graphic / minimal / masculine.

This is a wine made by three 35yr old guys

Target Market(s)

young & urban

Industry/Entity Type

Vineyard

Logo Text

Merlot & Cabernet / Ponte Capriasca / 2016

Font styles to use
Sans Serif

Requirements
Must have
• clearly legible
• aesthetically pleasing [minimalist]
• sans serif

```html
<!DOCTYPE html>
<html lang="en">
<head>
<meta charset="utf-8">
<title>Merlot &amp; Cabernet – Ponte Capriasca 2016</title>
<link rel="stylesheet" href="https://fonts.googleapis.com/css2?family=Josefin+Sans:wght@300&display=swap">
<style>
  :root {
    --wine-center: #762025;
    --wine-edge: #561e24;
    --label-cream: #fefbdc;
    --ink: #1e1c1a;
    --ink-soft: #3b3734;
  }
  html, body {
    margin: 0;
    padding: 0;
    width: 1200px;
    height: 1200px;
    overflow: hidden;
  }
  .canvas {
    position: relative;
    width: 1200px;
    height: 1200px;
    background: radial-gradient(circle at 50% 50%, var(--wine-center) 0%, var(--wine-edge) 75%);
  }
  .wine-label {
    position: absolute;
    left: 400px;
    top: 282px;
    width: 373px;
    height: 639px;
    background: var(--label-cream);
  }
  .emblem-area {
    position: absolute;
    left: 62px;
    top: 134px;
    width: 178px;
    height: 228px;
    background: radial-gradient(ellipse at 50% 50%, var(--ink-soft) 0%, var(--ink) 100%);
  }
  .label-text-art {
    position: absolute;
    left: 0;
    top: 0;
    width: 373px;
    height: 639px;
  }
  .label-text {
    font-family: 'Josefin Sans', sans-serif;
    font-weight: 300;
    fill: var(--ink);
    text-transform: uppercase;
  }
  .variety, .origin { font-size: 27px; }
  .vintage { font-size: 24px; }
  .vintage-rule {
    stroke: var(--ink);
    stroke-width: 1.6;
  }
</style>
</head>
<body>
  <main class="canvas">
    <section class="wine-label" aria-label="Wine label">
      <div class="emblem-area" role="img" aria-label="Hand-brushed open circle emblem in dark ink"></div>
      <svg class="label-text-art" viewBox="0 0 373 639" xmlns="http://www.w3.org/2000/svg">
        <text class="label-text variety" x="8" y="510" textLength="358" lengthAdjust="spacing">Merlot &amp; Cabarnet</text>
        <text class="label-text origin" x="22" y="546" textLength="326" lengthAdjust="spacing">Ponte Capriasca</text>
        <line class="vintage-rule" x1="0" y1="589" x2="156" y2="589"/>
        <line class="vintage-rule" x1="220" y1="589" x2="373" y2="589"/>
        <text class="label-text vintage" x="188" y="598" text-anchor="middle">2016</text>
      </svg>
    </section>
  </main>
</body>
</html>
```